Venture 482 - Lumora Book Cover

I am looking for a Lumora book cover for my book about "Venture 482".
The Book is Titled:
Venture 482 Ascended
Shaping Outcomes: Paths To Unlocking Cosmic Truths
Author is Dorian Pell
Here is a book description that may help you understand more about it:
Inspired by the genius of Edwin Marlowe, this comprehensive guide delves into the ancient wisdom and cutting-edge science behind the 482 method, a powerful tool for manifesting your desires. Whether you're seeking personal growth, financial success, or spiritual enlightenment, this book provides advanced techniques and methods to transform your dreams into reality.
Any questions please ask.
Thanks
Owen

```html
<!DOCTYPE html>
<html lang="en">
<head>
<meta charset="utf-8">
<title>Venture 482 Ascended — Dorian Pell</title>
<link rel="stylesheet" href="https://fonts.googleapis.com/css2?family=Bebas+Neue&family=Cinzel:wght@400&family=Crimson+Text:wght@400;700&family=Quicksand:wght@500&display=swap">
<style>
  :root {
    --night-top: #2b2036;
    --night-mid: #221830;
    --night-deep: #180f1f;
    --ink-white: #f4f1f4;
    --mist: #d9d3de;
    --blush: #f3ddd4;
  }
  * { margin: 0; padding: 0; box-sizing: border-box; }
  html, body {
    width: 805px; height: 1200px; overflow: hidden;
    background: var(--night-deep);
  }
  .cover {
    position: relative;
    width: 805px; height: 1200px; overflow: hidden;
    background:
      radial-gradient(ellipse at 30% 8%, #4a3c58 0%, transparent 45%),
      linear-gradient(180deg, var(--night-top) 0%, var(--night-mid) 50%, var(--night-deep) 100%);
    color: var(--ink-white);
  }
  .sigil {
    position: absolute;
    left: 85px; top: 168px;
    width: 640px; height: 640px;
  }
  .series-title {
    position: absolute;
    left: 0; right: 0; top: 150px;
    text-align: center;
    font-family: "Bebas Neue", sans-serif;
    font-size: 196px;
    line-height: 1;
    letter-spacing: 2px;
    color: var(--ink-white);
    text-shadow: 0 6px 14px rgba(0,0,0,.45);
  }
  .series-number {
    position: absolute;
    left: 0; right: 0; top: 438px;
    text-align: center;
    font-family: "Quicksand", sans-serif;
    font-weight: 500;
    font-size: 96px;
    line-height: 1;
    color: var(--ink-white);
  }
  .edition {
    position: absolute;
    left: 118px; right: 86px; top: 797px;
    display: flex; justify-content: space-between;
    font-family: "Bebas Neue", sans-serif;
    font-size: 64px;
    line-height: 1;
    color: var(--mist);
  }
  .subtitle {
    position: absolute;
    left: 0; right: 0; top: 920px;
    text-align: center;
    font-family: "Crimson Text", serif;
    color: var(--ink-white);
  }
  .subtitle .lead {
    display: block;
    font-weight: 700;
    font-size: 25px;
    line-height: 34px;
    text-transform: uppercase;
  }
  .subtitle .rest {
    display: block;
    font-weight: 400;
    font-size: 26px;
    line-height: 35px;
  }
  .author {
    position: absolute;
    left: 50px; right: 42px; top: 1130px;
    display: flex; justify-content: space-between;
    font-family: "Cinzel", serif;
    font-size: 62px;
    line-height: 1;
    color: var(--blush);
  }
  .author .gap { width: 40px; }
</style>
</head>
<body>
<main class="cover">
  <svg class="sigil" viewBox="0 0 640 640" role="img" aria-label="Sacred geometry mandala: a white ring of interlocking triangles and eye motifs surrounded by faint handwritten numerals and star points">
    <defs>
      <radialGradient id="sigil-fill" cx="50%" cy="50%" r="50%">
        <stop offset="0%" stop-color="#2a1f34"/>
        <stop offset="70%" stop-color="#4b3e57"/>
        <stop offset="86%" stop-color="#d8d0dc"/>
        <stop offset="100%" stop-color="#efeaf0"/>
      </radialGradient>
    </defs>
    <circle cx="320" cy="330" r="228" fill="url(#sigil-fill)"/>
  </svg>

  <h1 class="series-title">VENTURE</h1>
  <div class="series-number">482</div>

  <div class="edition" aria-label="Ascended">
    <span>A</span><span>S</span><span>C</span><span>E</span><span>N</span><span>D</span><span>E</span><span>D</span>
  </div>

  <p class="subtitle">
    <span class="lead">Shaping Outcomes:</span>
    <span class="rest">Paths to unlocking</span>
    <span class="rest">cosmic truths</span>
  </p>

  <div class="author" aria-label="Dorian Pell">
    <span>D</span><span>O</span><span>R</span><span>I</span><span>A</span><span>N</span><span class="gap"></span><span>P</span><span>E</span><span>L</span><span>L</span>
  </div>
</main>
</body>
</html>
```